Harbor Wonder Hour - A magic website for a monthly modern magic show

Looking to build a website to promote my new monthly magic show

Sites like this. https://velvetloftshow.example/ https://sevencuriouscardsnight.example/

Target Market(s)

18-65 year old men and women who enjoy live entertainment especially magic

Industry/Entity Type

Entertainment

Coding

Coded - Design and coding required

Number of Pages Required

3 page

Colors

Designer to choose colors to be used in the design.

Requirements
Must have
• Wanting a wordpress site.
• Contact form, media section for photos and videos to be posted.
• A “reviews/testimonials” section.

```html
<!DOCTYPE html>
<html lang="en">
<head>
<meta charset="utf-8">
<title>Harbor Wonder Hour</title>
<link rel="stylesheet" href="https://fonts.googleapis.com/css2?family=Montserrat:wght@400;500;600;700;800&display=swap">
<style>
:root{
  --gold:#c9954c;
  --ink:#151515;
  --panel:#1b1b1b;
  --footer:#2a2a2a;
  --text:#f2f2f2;
  --muted:#d6d6d6;
}
*{box-sizing:border-box;margin:0;padding:0}
html,body{width:1200px;height:4073px;overflow:hidden}
body{background:var(--panel);color:var(--text);font-family:'Montserrat',sans-serif;position:relative}
.abs{position:absolute}
a{color:inherit;text-decoration:none}
.btn{position:absolute;display:flex;align-items:center;justify-content:center;gap:10px;height:54px;border-radius:27px;background:var(--gold);color:#1a1a1a;font-weight:700;font-size:16px;letter-spacing:.3px;text-transform:uppercase}
.btn.outline{background:transparent;border:2px solid var(--gold);color:var(--gold)}
.btn .arrow{width:16px;height:16px}
.section-title{position:absolute;left:0;width:1200px;text-align:center;color:var(--gold);font-weight:700;font-size:36px;letter-spacing:.5px;text-transform:uppercase}
.copy{font-size:15.5px;line-height:36px;text-align:justify;color:var(--text)}

.site-header{position:absolute;top:0;left:0;width:1200px;height:155px;background:var(--ink)}
.call{position:absolute;left:234px;top:28px;display:flex;gap:12px;align-items:center}
.call-label{font-size:15px;color:var(--gold)}
.call-number{font-size:16px;font-weight:700;color:var(--gold)}
.nav a{position:absolute;top:101px;font-size:17px;color:var(--gold)}
.brand{position:absolute;left:520px;top:40px;width:160px;display:flex;align-items:center;gap:8px;color:var(--gold);font-weight:700;font-size:14px;line-height:18px;text-transform:uppercase}
.brand-dot{width:14px;height:14px;border-radius:50%;background:var(--gold);flex:none}

.hero{position:absolute;top:155px;left:0;width:1200px;height:650px;background:linear-gradient(100deg,#6c6c6a 0%,#3d3b39 35%,#6a6865 70%,#4a4846 100%)}
.hero-tag{position:absolute;left:700px;font-size:19px;font-weight:600}
.hero-title{position:absolute;left:700px;font-size:37px;font-weight:600;color:var(--gold)}

.about-title{position:absolute;left:574px;top:1340px;font-size:36px;font-weight:700;color:var(--gold);text-transform:uppercase}
.about-copy{position:absolute;left:574px;top:1392px;width:537px;font-size:13px;line-height:36px}

.gallery{position:absolute;top:1802px;left:0;width:1200px;height:1200px;background:linear-gradient(180deg,#2a2422 0%,#1f1a19 50%,#231c1a 100%)}
.tile{position:absolute}

.quote-copy{position:absolute;left:384px;top:3198px;width:672px;font-size:15px;line-height:32px;text-align:justify}
.quote-mark{position:absolute;font-size:110px;font-weight:800;color:var(--gold);line-height:1}

.site-footer{position:absolute;top:3502px;left:0;width:1200px;height:571px;background:var(--footer)}
.foot-head{position:absolute;top:3790px;font-size:21px;font-weight:700;color:var(--gold);text-transform:uppercase}
.links{position:absolute;left:88px;top:3830px;list-style:none}
.links li{font-size:15px;line-height:28.6px}
.links li::before{content:"»";margin-right:10px}
.contact-list{position:absolute;left:373px;top:3828px;width:300px;list-style:none;font-size:15px;line-height:27px;color:var(--muted)}
.contact-list li{display:flex;gap:12px}
.contact-list svg{flex:none;margin-top:7px}
.field{position:absolute;height:41px;border:2px solid #e5e5e5;color:#e5e5e5;font:500 14px 'Montserrat',sans-serif;padding-left:10px;display:flex;align-items:center}
.submit{position:absolute;left:911px;top:3924px;width:199px;height:41px;background:var(--gold);color:#1a1a1a;font-weight:700;font-size:15px;display:flex;align-items:center;justify-content:center}
.copyright{position:absolute;top:4028px;left:0;width:1200px;text-align:center;font-size:16px}
</style>
</head>
<body>

<svg width="0" height="0" style="position:absolute">
  <defs>
    <symbol id="arrow" viewBox="0 0 16 16"><circle cx="8" cy="8" r="8" fill="currentColor"/><path d="M4 8h6M8 5l3 3-3 3" stroke="#c9954c" stroke-width="2" fill="none"/></symbol>
  </defs>
</svg>

<header class="site-header">
  <div class="call">
    <svg width="40" height="40" viewBox="0 0 40 40"><circle cx="20" cy="20" r="18" fill="none" stroke="#c9954c" stroke-width="2.5"/><path d="M13 11c2-1 3 0 4 3s-1 3-1 4 3 5 5 6 2-1 4-1 3 2 2 4-3 2-5 1-7-5-8-9-2-7-1-8z" fill="#c9954c"/></svg>
    <div><div class="call-label">Call Us:</div><div class="call-number">555-014-2288</div></div>
  </div>
  <nav class="nav">
    <a style="left:165px">Home</a>
    <a style="left:257px">About</a>
    <a style="left:349px">Private Events</a>
    <a style="left:706px">Corporate Events</a>
    <a style="left:888px">Reviews</a>
    <a style="left:997px">Contact</a>
  </nav>
  <div class="brand"><span class="brand-dot"></span><span>Julian Marlowe Magic</span></div>
  <a class="btn" style="left:784px;top:28px;width:199px;height:46px;font-size:15px">Book a Ticket <svg class="arrow" style="color:#1a1a1a"><use href="#arrow"/></svg></a>
</header>

<section class="hero">
  <div role="img" aria-label="Magician in a suit throwing playing cards toward the camera" style="position:absolute;inset:0"></div>
  <p class="hero-tag" style="top:205px">More than Entertainment – An Experience</p>
  <h1 class="hero-title" style="top:240px">Award Winning Magic</h1>
  <a class="btn" style="left:700px;top:303px;width:232px">Our Services <svg class="arrow" style="color:#1a1a1a"><use href="#arrow"/></svg></a>
</section>

<svg class="abs" style="left:0;top:700px" width="1200" height="110" viewBox="0 0 1200 110">
  <path d="M0 110 L0 100 Q600 0 1200 100 L1200 110 Z" fill="#1b1b1b"/>
  <path d="M110 85 Q600 10 1090 85" fill="none" stroke="#c9954c" stroke-width="5"/>
  <circle cx="600" cy="37" r="22" fill="#1b1b1b" stroke="#c9954c" stroke-width="2"/>
</svg>

<h2 class="section-title" style="top:880px">Welcome to Harbor Wonder Hour</h2>
<p class="copy abs" style="left:150px;top:932px;width:900px">Sed ut perspiciatis unde omnis iste natus error sit voluptatem accusantium doloremque laudantium, totam rem aperiam, eaque ipsa quae ab illo inventore veritatis et quasi architecto beatae vitae dicta sunt explicabo. Nemo enim <span style="display:block;text-align:center">ipsam voluptatem quia magni dolores eos qui ratione voluptatem sequi nesciunt.</span></p>
<a class="btn" style="left:372px;top:1063px;width:233px">Check Availability <svg class="arrow" style="color:#1a1a1a"><use href="#arrow"/></svg></a>
<a class="btn outline" style="left:622px;top:1063px;width:206px">Book Now <svg class="arrow" style="color:#c9954c"><use href="#arrow"/></svg></a>

<svg class="abs" style="left:85px;top:1270px" width="450" height="450" viewBox="0 0 450 450">
  <circle cx="225" cy="225" r="205" fill="none" stroke="#c9954c" stroke-width="18" stroke-dasharray="260 60"/>
  <circle cx="223" cy="224" r="183" fill="#3f6f95" stroke="#c9954c" stroke-width="4"/>
</svg>
<div class="abs" role="img" aria-label="Portrait of the magician in a white shirt and dark vest" style="left:127px;top:1313px;width:362px;height:362px;border-radius:50%;background:radial-gradient(circle at 50% 40%,#6a9ec4,#2d5577)"></div>

<h2 class="about-title">About Julian Marlowe</h2>
<p class="copy about-copy">Sed ut perspiciatis unde omnis iste natus error sit voluptatem accusantium doloremque laudantium, totam rem aperiam, eaque ipsa quae ab illo inventore veritatis et quasi architecto beatae vitae dicta sunt explicabo. Nemo enim ipsam voluptatem quia voluptas sit aspernatur aut odit aut fugit, sed quia consequuntur magni dolores eos qui ratione voluptatem sequi nesciunt.</p>
<a class="btn" style="left:574px;top:1586px;width:206px">Read More <svg class="arrow" style="color:#1a1a1a"><use href="#arrow"/></svg></a>

<section class="gallery" role="img" aria-label="Dim background photo of guests at a magic show"></section>
<svg class="abs" style="left:0;top:1795px" width="1200" height="70" viewBox="0 0 1200 70">
  <path d="M0 0 L1200 0 L1200 10 Q600 80 0 10 Z" fill="#1b1b1b"/>
  <path d="M110 22 Q600 80 1090 22" fill="none" stroke="#c9954c" stroke-width="5"/>
</svg>
<h2 class="section-title" style="top:1946px">Our Gallery</h2>
<div class="tile" role="img" aria-label="Magician showing a card at a party table" style="left:87px;top:2024px;width:496px;height:269px;background:linear-gradient(135deg,#d9d2c4,#b9397e 45%,#3f5a3a)"></div>
<div class="tile" role="img" aria-label="Video still of the magician fanning cards" style="left:604px;top:2024px;width:506px;height:498px;background:linear-gradient(135deg,#8a8a8a,#d8d8d8 50%,#6d6d6d)">
  <svg class="abs" style="left:225px;top:219px" width="60" height="66" viewBox="0 0 60 66"><path d="M2 2 L58 33 L2 64 Z" fill="#111"/></svg>
</div>
<div class="tile" role="img" aria-label="Guests holding cards at a dinner table" style="left:90px;top:2316px;width:237px;height:435px;background:linear-gradient(180deg,#b28a4c,#6d4e35 55%,#1e2a55)"></div>
<div class="tile" role="img" aria-label="Black and white stage performance" style="left:348px;top:2316px;width:237px;height:206px;background:linear-gradient(180deg,#5a5a5a,#1e1e1e)"></div>
<div class="tile" role="img" aria-label="Party guests under pink feather decor" style="left:348px;top:2542px;width:237px;height:209px;background:linear-gradient(135deg,#c23a8c,#3f7a6e 50%,#5b4a3f)"></div>
<div class="tile" role="img" aria-label="Magician performing for seated guests" style="left:604px;top:2542px;width:245px;height:209px;background:linear-gradient(135deg,#a44d7a,#5e5a4f 55%,#2f2f2f)"></div>
<div class="tile" role="img" aria-label="Crowd gathered in an industrial venue" style="left:865px;top:2542px;width:245px;height:209px;background:linear-gradient(180deg,#8a6a3e,#4a3a2a)"></div>
<a class="btn" style="left:509px;top:2797px;width:182px;height:48px">View More <svg class="arrow" style="color:#1a1a1a"><use href="#arrow"/></svg></a>

<svg class="abs" style="left:0;top:2930px" width="1200" height="75" viewBox="0 0 1200 75">
  <path d="M0 75 L0 65 Q600 -10 1200 65 L1200 75 Z" fill="#1b1b1b"/>
  <path d="M110 55 Q600 -5 1090 55" fill="none" stroke="#c9954c" stroke-width="5"/>
</svg>

<h2 class="section-title" style="top:3075px">Testimonials</h2>
<div class="abs" style="left:113px;top:3152px;width:194px;height:194px;border-radius:50%;border:4px solid #c9954c;background:#1b1b1b"></div>
<div class="abs" role="img" aria-label="Portrait of a smiling reviewer" style="left:123px;top:3162px;width:174px;height:174px;border-radius:50%;background:radial-gradient(circle at 50% 40%,#c9a48a,#5e4a3e)"></div>
<span class="quote-mark" style="left:328px;top:3140px">“</span>
<span class="quote-mark" style="left:1033px;top:3265px">”</span>
<p class="quote-copy">Sed ut perspiciatis unde omnis iste natus error sit voluptatem accusantium doloremque laudantium, totam rem aperiam, eaque ipsa quae ab illo inventore veritatis et quasi architecto beatae vitae dicta sunt explicabo.<br><strong>- Hartwell</strong></p>

<footer class="site-footer"></footer>
<svg class="abs" style="left:0;top:3490px" width="1200" height="80" viewBox="0 0 1200 80">
  <path d="M0 0 L1200 0 L1200 12 Q600 90 0 12 Z" fill="#1b1b1b"/>
  <path d="M110 25 Q600 85 1090 25" fill="none" stroke="#c9954c" stroke-width="5"/>
</svg>
<div class="brand" style="top:3672px;left:520px"><span class="brand-dot"></span><span>Julian Marlowe Magic</span></div>

<h3 class="foot-head" style="left:88px">Quick Links</h3>
<ul class="links">
  <li>Home</li><li>Corporate Events</li><li>Private Events</li><li>About</li><li>Reviews</li><li>Contact</li>
</ul>

<h3 class="foot-head" style="left:373px">Contact Us</h3>
<ul class="contact-list">
  <li><svg width="14" height="16" viewBox="0 0 14 16"><path d="M7 0a6 6 0 0 0-6 6c0 4 6 10 6 10s6-6 6-10a6 6 0 0 0-6-6z" fill="#e5e5e5"/><circle cx="7" cy="6" r="2.2" fill="#2a2a2a"/></svg><span>12 Lantern Row, Pier District, WA 98101</span></li>
  <li><svg width="14" height="14" viewBox="0 0 14 14"><path d="M2 1c2-1 3 1 3 3s-1 2 0 3 2 3 3 3 1-1 3 0 2 2 1 3-4 1-7-2-4-8-3-10z" fill="#e5e5e5"/></svg><span>Phone : 555-014-2288</span></li>
  <li><svg width="14" height="12" viewBox="0 0 14 12"><rect width="14" height="12" rx="1" fill="#e5e5e5"/><path d="M1 2l6 5 6-5" stroke="#2a2a2a" stroke-width="1.4" fill="none"/></svg><span>Email :<br>info@julianmarlowemagic.example</span></li>
</ul>

<h3 class="foot-head" style="left:700px;top:3786px">Get In Touch</h3>
<p class="abs" style="left:700px;top:3828px;font-size:12px">Alternatively You Can Fill In the Following Contact Form:</p>
<div class="field" style="left:701px;top:3869px;width:199px">NAME</div>
<div class="field" style="left:911px;top:3869px;width:199px">EMAIL</div>
<div class="field" style="left:701px;top:3924px;width:199px">PHONE</div>
<div class="submit">SUBMIT</div>

<p class="copyright">Copyright © 2019. All Rights Reserved</p>

</body>
</html>
```